we can communicate on this, but i want to follow the approach we took on Pellew|Marsh & Quinlan but i feel the card front needs the black background and the platinum and gold logo. The back? I am open. we can use the same info from PM&Q. Velmont Arc is an enhanced equity investment fund - basically a very exclusive boutique hedge fund that uses only stock options. very advanced things. hope you are interested

Contact Information for Business Card

Dr. Lewis T. Brennick, CFA
Scientifique de fusée financière
701.555.0143
LTBquant47@mailvantor.com

4718 Willow Creek Bend W.
West Fargo, ND 58078

No web site

Colors

Designer to choose colors to be used in the design.

Requirements
Nice to have
• I tend to prefer the most visible applications of the logo to include logo and name, the logo version with a black background and the gold and platinum components separated by the black. I see this working well for a single side (logo and name - this is card front to me).
• I am fairly open to other treatments on the reverse side with the data. To me, it makes sense to have a different color rendition of the logo on the reverse and it may be a muted black tone on tone or an oversized portion that would have spot UV. Or, the reverse may play with colors and layout
Should not have
• Other colors = no no
• Decorative font

```html
<!DOCTYPE html>
<html lang="en">
<head>
<meta charset="utf-8">
<title>Velmont Arc — Business Card</title>
<link href="https://fonts.googleapis.com/css2?family=Montserrat:wght@400;500;700&display=swap" rel="stylesheet">
<style>
  :root {
    --page: #e9e9e7;
    --card-black: #232323;
    --card-white: #ffffff;
    --gold: #c9a52f;
    --ink: #151515;
    --text: #222222;
  }
  * { box-sizing: border-box; margin: 0; padding: 0; }
  html, body { width: 1200px; height: 912px; overflow: hidden; }
  body {
    background: var(--page);
    font-family: "Montserrat", Arial, sans-serif;
    display: flex;
    flex-direction: column;
    align-items: center;
    justify-content: center;
    gap: 56px;
  }
  .card {
    width: 620px;
    height: 354px;
    border-radius: 22px;
    position: relative;
    overflow: hidden;
    box-shadow: 0 6px 18px rgba(0,0,0,.15);
  }
  /* Front: black with brand */
  .card--front {
    background: var(--card-black);
    display: flex;
    align-items: center;
    justify-content: center;
    gap: 18px;
  }
  .brand-dot {
    width: 54px; height: 54px;
    border-radius: 50%;
    background: var(--gold);
    flex: none;
  }
  .card--front .brand-name {
    color: var(--gold);
    font-weight: 700;
    font-size: 34px;
    letter-spacing: 1px;
    text-transform: uppercase;
  }
  /* Back: white with details */
  .card--back { background: var(--card-white); }
  .back-brand {
    position: absolute;
    left: 28px; top: 112px;
    width: 250px;
    display: flex;
    flex-direction: column;
    align-items: center;
    gap: 16px;
  }
  .back-brand .brand-dot { width: 78px; height: 78px; }
  .back-brand .brand-name {
    color: var(--ink);
    font-weight: 700;
    font-size: 30px;
    letter-spacing: .5px;
    text-transform: uppercase;
    white-space: nowrap;
  }
  .divider {
    position: absolute;
    left: 296px; top: 62px;
    width: 1.5px; height: 180px;
    background: var(--gold);
  }
  .details {
    position: absolute;
    left: 318px; top: 50px;
    width: 286px;
    color: var(--text);
    font-size: 13.5px;
    line-height: 1.4;
  }
  .details .person {
    color: var(--gold);
    font-weight: 500;
    font-size: 15px;
    text-transform: uppercase;
    line-height: 1.2;
    white-space: nowrap;
  }
  .details .role { margin-bottom: 10px; }
  .details .address { margin-bottom: 10px; }
  .contact-list { list-style: none; }
  .contact-list li { display: flex; align-items: center; gap: 8px; white-space: nowrap; }
  .contact-list svg { width: 11px; height: 11px; flex: none; }
  .wave {
    position: absolute;
    left: 0; bottom: 0;
    width: 620px; height: 354px;
  }
</style>
</head>
<body>
  <section class="card card--front" aria-label="Card front">
    <span class="brand-dot" aria-hidden="true"></span>
    <span class="brand-name">Velmont Arc</span>
  </section>

  <section class="card card--back" aria-label="Card back">
    <svg class="wave" viewBox="0 0 620 354" aria-hidden="true">
      <path d="M262 354 C380 330 450 285 620 262 L620 272 C455 295 390 338 288 354 Z" fill="var(--ink)"/>
      <path d="M288 354 C390 338 455 295 620 272 L620 354 Z" fill="var(--gold)"/>
    </svg>

    <div class="back-brand">
      <span class="brand-dot" aria-hidden="true"></span>
      <span class="brand-name">Velmont Arc</span>
    </div>

    <div class="divider" aria-hidden="true"></div>

    <div class="details">
      <p class="person">Dr. Lewis T. Brennick, CFA</p>
      <p class="role">Scientifique de fusée financière</p>
      <p class="address">4718 Willow Creek Bend W.<br>West Fargo, ND 58078</p>
      <ul class="contact-list">
        <li>
          <svg viewBox="0 0 12 12"><path d="M2.5 1 L4.5 1 L5.2 3.6 L3.9 4.6 C4.6 6 5.8 7.3 7.3 8 L8.3 6.8 L11 7.5 L11 9.5 C11 10.3 10.3 11 9.5 11 C5 11 1 7 1 2.5 C1 1.7 1.7 1 2.5 1 Z" fill="var(--gold)"/></svg>
          701.555.0143
        </li>
        <li>
          <svg viewBox="0 0 12 12"><rect x="1" y="2.5" width="10" height="7" fill="none" stroke="var(--gold)" stroke-width="1.2"/><path d="M1 2.5 L6 6.5 L11 2.5" fill="none" stroke="var(--gold)" stroke-width="1.2"/></svg>
          LTBquant47@mailvantor.com
        </li>
      </ul>
    </div>
  </section>
</body>
</html>
```